Business Card for Industrial Distributor

We need a business card design for an industrial distributor. We sell machine parts for the manufacturing and oil industry. We would like the cards to look clean and modern but with a touch of industry.

Our colors are blue/white.

Please feel free to visit our website www.korvelpartsco.com

Target Market(s)

mexican manufacturers in the automobile/aerospace industry

Industry/Entity Type

Industrial

Colors
ffffff
0555a3

```html
<!DOCTYPE html>
<html lang="en">
<head>
<meta charset="utf-8">
<title>Korvel Parts Co. Business Card</title>
<link href="https://fonts.googleapis.com/css2?family=Lato:wght@400;700;900&display=swap" rel="stylesheet">
<style>
  :root {
    --brand-blue: #3a4594;
    --band-grey: #9a9b9d;
    --frame-grey: #8a8b8e;
    --text-grey: #6d6e71;
    --logo-grey: #6d6e71;
    --paper: #ffffff;
  }
  * { margin: 0; padding: 0; box-sizing: border-box; }
  html, body {
    width: 1200px; height: 761px; overflow: hidden;
    background: var(--paper);
    font-family: 'Lato', sans-serif;
  }
  .canvas { position: relative; width: 1200px; height: 761px; }
  .card {
    position: absolute; top: 206px; width: 460px; height: 299px;
    background: var(--paper);
    border-left: 1px solid var(--frame-grey);
    border-right: 1px solid var(--frame-grey);
    overflow: hidden;
  }
  .card--front { left: 115px; }
  .card--back { left: 590px; }
  .band-top { position: absolute; top: 0; left: 0; right: 0; height: 9px; background: var(--brand-blue); }
  .band-grey { position: absolute; top: 238px; left: 0; right: 0; height: 51px; background: var(--band-grey); }
  .band-bottom { position: absolute; bottom: 0; left: 0; right: 0; height: 10px; background: var(--brand-blue); }

  .partner-name {
    position: absolute; top: 22px; right: 28px;
    font-size: 26px; font-weight: 700; color: var(--logo-grey);
    letter-spacing: 0.2px;
  }

  .contact-list { position: absolute; left: 31px; top: 123px; list-style: none; }
  .contact-item {
    width: 190px; height: 27px; margin-bottom: 13px;
    border: 2px solid var(--band-grey);
    display: flex; align-items: center;
    font-size: 10.5px; color: var(--text-grey);
  }
  .contact-item svg { width: 12px; height: 12px; margin: 0 12px 0 8px; flex: none; }

  .brand {
    position: absolute; top: 110px; left: 76px;
    display: flex; align-items: center;
  }
  .brand-mark {
    width: 54px; height: 54px; border-radius: 50%;
    background: var(--brand-blue);
    margin-right: 16px;
  }
  .brand-name {
    font-size: 50px; font-weight: 900; color: var(--brand-blue);
    letter-spacing: 0.5px;
  }
  .back-url {
    position: absolute; top: 238px; left: 0; right: 0; height: 51px;
    padding-top: 8px;
    display: flex; align-items: center; justify-content: center;
    font-size: 15px; color: var(--paper);
  }
</style>
</head>
<body>
<div class="canvas">
  <section class="card card--front">
    <div class="band-top"></div>
    <div class="partner-name">Velmora Systems</div>
    <ul class="contact-list">
      <li class="contact-item">
        <svg viewBox="0 0 12 12"><rect x="1" y="3" width="10" height="6" fill="none" stroke="#6d6e71" stroke-width="1"/><path d="M1 3 L6 7 L11 3" fill="none" stroke="#6d6e71" stroke-width="1"/></svg>
        contact@velmorasystems.net
      </li>
      <li class="contact-item">
        <svg viewBox="0 0 12 12"><path d="M3 1.5 L5 3.5 L4 5 Q5 7 7 8 L8.5 7 L10.5 9 L9 10.5 Q5 10.5 1.5 3 Z" fill="#6d6e71"/></svg>
        +333 22 222 2222
      </li>
      <li class="contact-item">
        <svg viewBox="0 0 12 12"><circle cx="6" cy="6" r="4.8" fill="none" stroke="#6d6e71" stroke-width="1.2"/><path d="M6 1.2 Q3.5 6 6 10.8 M6 1.2 Q8.5 6 6 10.8 M1.2 6 H10.8" fill="none" stroke="#6d6e71" stroke-width="0.8"/></svg>
        www.korvelpartsco.com
      </li>
    </ul>
    <div class="band-grey"></div>
    <div class="band-bottom"></div>
  </section>

  <section class="card card--back">
    <div class="band-top"></div>
    <div class="brand">
      <div class="brand-mark"></div>
      <div class="brand-name">Korvel</div>
    </div>
    <div class="band-grey"></div>
    <div class="back-url">www.korvelpartsco.com</div>
    <div class="band-bottom"></div>
  </section>
</div>
</body>
</html>
```